full stationary design for a modern sleek design company

we are a design company that does modern minimalistic interior design works as well as other design services for high end clients.
we need a full stationary design including and not limited to (double sided business card, letter head, envelopes, documents folder...etc) that reflects the modern style design we do.
sleek modern and minimalistic is the requirements.
Updates

please use the latest attached files as there was a slight modification on the logo Added Wednesday, March 1, 2017

minor update on the logo files in JPG and PSD has been updated kindly follow the new attachments. Added Thursday, March 2, 2017

Target Market(s)

modern minimalist clients

Industry/Entity Type

Design Agency

Requirements
Must have
• the logo
Nice to have
• i like the colors in the colored 3D logo attached
Should not have
• too many colors

```html
<!DOCTYPE html>
<html lang="en">
<head>
<meta charset="utf-8">
<title>Norvale Studio – Business Card</title>
<link rel="stylesheet" href="https://fonts.googleapis.com/css2?family=Open+Sans:wght@400;600;700&display=swap">
<style>
  :root {
    --backdrop: #3a3a3a;
    --paper: #ffffff;
    --charcoal: #2b2b2b;
    --orange: #ef8a1c;
    --light-text: #f2f2f2;
  }
  * { margin: 0; padding: 0; box-sizing: border-box; }
  html, body { width: 1200px; height: 750px; overflow: hidden; }
  body {
    background: var(--backdrop);
    font-family: "Open Sans", sans-serif;
    position: relative;
  }
  .card {
    position: absolute;
    top: 228px;
    width: 462px;
    height: 262px;
    border-radius: 14px;
    overflow: hidden;
  }
  .card-front { left: 124px; background: var(--paper); }
  .card-back { left: 618px; background: var(--orange); }
  .card-wave { position: absolute; inset: 0; width: 100%; height: 100%; }

  .brand {
    position: absolute;
    left: 0; right: 0;
    display: flex;
    align-items: center;
    justify-content: center;
    gap: 10px;
  }
  .brand-mark { width: 22px; height: 22px; }
  .brand-name {
    font-weight: 700;
    font-size: 26px;
    letter-spacing: 2px;
    color: var(--charcoal);
    text-transform: uppercase;
  }
  .card-front .brand { top: 44px; }
  .card-front .brand-mark { background: var(--orange); }
  .card-back .brand { top: 113px; }
  .card-back .brand-mark { background: var(--charcoal); }

  .holder {
    position: absolute;
    right: 250px;
    top: 158px;
    text-align: right;
    color: var(--light-text);
    font-size: 12.5px;
    line-height: 18px;
  }
  .holder-name {
    color: var(--orange);
    font-size: 17px;
    font-weight: 600;
    line-height: 22px;
  }
  .divider {
    position: absolute;
    left: 226px;
    top: 160px;
    width: 1px;
    height: 70px;
    background: #777;
  }
  .contacts {
    position: absolute;
    left: 238px;
    top: 160px;
    list-style: none;
    color: var(--light-text);
    font-size: 12.5px;
    line-height: 17.6px;
  }
  .contacts li { display: flex; align-items: center; gap: 7px; }
  .contacts svg { width: 12px; height: 12px; flex: none; }
</style>
</head>
<body>
  <section class="card card-front">
    <svg class="card-wave" viewBox="0 0 462 262" preserveAspectRatio="none" aria-hidden="true">
      <path d="M0,112 C70,130 150,130 240,118 C320,106 400,104 462,122 L462,132 C400,114 320,116 240,128 C150,140 70,140 0,122 Z" fill="var(--orange)"/>
      <path d="M0,126 C70,146 150,146 240,132 C320,120 400,118 462,136 L462,262 L0,262 Z" fill="var(--charcoal)"/>
    </svg>
    <div class="brand">
      <span class="brand-mark"></span>
      <span class="brand-name">Norvale Studio</span>
    </div>
    <div class="holder">
      <p class="holder-name">CLARA HENSLEY</p>
      <p>CEO&amp;Founder</p>
      <p>42 Birchwood Avenue</p>
      <p>Fairmont, Oregon 97120</p>
    </div>
    <div class="divider"></div>
    <ul class="contacts">
      <li>
        <svg viewBox="0 0 12 12"><path d="M2,1 L4.5,1 L5.3,3.6 L4,4.6 C4.7,6 6,7.3 7.4,8 L8.4,6.7 L11,7.5 L11,10 C11,10.6 10.6,11 10,11 C5,11 1,7 1,2 C1,1.4 1.4,1 2,1 Z" fill="var(--orange)"/></svg>
        (555) 214 7730
      </li>
      <li>
        <svg viewBox="0 0 12 12"><rect x="2.5" y="0.5" width="7" height="11" rx="1" fill="var(--orange)"/><rect x="3.8" y="2" width="4.4" height="7" fill="var(--charcoal)"/></svg>
        (555) 306 4182
      </li>
      <li>
        <svg viewBox="0 0 12 12"><rect x="0.5" y="2.5" width="11" height="7.5" fill="var(--orange)"/><path d="M0.5,2.5 L6,7 L11.5,2.5" fill="none" stroke="var(--charcoal)" stroke-width="1"/></svg>
        clara@norvalestudio.com
      </li>
      <li>
        <svg viewBox="0 0 12 12"><circle cx="6" cy="6" r="5.5" fill="var(--orange)"/><path d="M1,6 H11 M6,0.5 C3.5,3 3.5,9 6,11.5 M6,0.5 C8.5,3 8.5,9 6,11.5" fill="none" stroke="var(--charcoal)" stroke-width="0.8"/></svg>
        www.norvalestudio.com
      </li>
    </ul>
  </section>

  <section class="card card-back">
    <div class="brand">
      <span class="brand-mark"></span>
      <span class="brand-name">Norvale Studio</span>
    </div>
  </section>
</body>
</html>
```